business card

Business card for new business.
Red and black corporate colors.
Card can have an Indsutrial feel to it. Feel free to add Rust, Bolted steel, or graphics as you see fit. We provide highly specialized services to the below mentioned industries.
Keep information out of corners so that if I want I can choose rounded corners.
Information
- front. name - title - phone - email
- Rear
Pipelines - Rail - Infrastructure - Forestry - Power
Northgate - Ridgeford - Port Alderby - Cedarvale - Westhaven

```html
<!DOCTYPE html>
<html lang="en">
<head>
<meta charset="utf-8">
<title>Girderline business card</title>
<link href="https://fonts.googleapis.com/css2?family=Roboto:wght@400;500&family=Roboto+Condensed:wght@700&display=swap" rel="stylesheet">
<style>
  :root {
    --backdrop: #5a4a3b;
    --card-front: #f3f3f3;
    --card-back: #808080;
    --brand-red: #e30613;
    --steel-grey: #7a7a7a;
    --text-dark: #4a4a4a;
    --white: #ffffff;
  }
  html, body {
    margin: 0;
    padding: 0;
    width: 1200px;
    height: 960px;
    overflow: hidden;
    background: var(--backdrop);
  }
  .canvas {
    position: relative;
    width: 1200px;
    height: 960px;
  }
  .card {
    position: absolute;
    width: 600px;
    height: 343px;
    box-shadow: 2px 3px 4px rgba(0, 0, 0, 0.45);
  }
  .card-front {
    left: 314px;
    top: 113px;
    background: var(--card-front);
  }
  .card-back {
    left: 311px;
    top: 472px;
    background: var(--card-back);
  }
  .brand {
    position: absolute;
    right: 46px;
    top: 58px;
    display: flex;
    align-items: center;
    gap: 10px;
    font-family: "Roboto Condensed", "Arial Narrow", sans-serif;
    font-weight: 700;
    font-size: 44px;
    line-height: 1;
    color: var(--steel-grey);
    letter-spacing: 0.5px;
  }
  .brand-square {
    width: 14px;
    height: 14px;
    background: var(--brand-red);
  }
  .name-flag {
    position: absolute;
    left: 0;
    top: 190px;
  }
  .person {
    position: absolute;
    left: 44px;
    top: 187px;
  }
  .person-name {
    margin: 0;
    font-family: "Roboto Condensed", "Arial Narrow", sans-serif;
    font-weight: 700;
    font-size: 24px;
    color: var(--brand-red);
    line-height: 1.1;
  }
  .person-title {
    margin: 2px 0 0;
    font-family: "Roboto", Arial, sans-serif;
    font-weight: 500;
    font-size: 15px;
    color: var(--steel-grey);
  }
  .contact-list {
    position: absolute;
    left: 46px;
    top: 251px;
    margin: 0;
    padding: 0;
    list-style: none;
    font-family: "Roboto", Arial, sans-serif;
    font-size: 14px;
    color: var(--text-dark);
  }
  .contact-list li {
    display: flex;
    align-items: center;
    gap: 9px;
    height: 19px;
  }
  .contact-icon {
    width: 13px;
    height: 13px;
    flex: none;
  }
  .back-brand {
    position: absolute;
    left: 0;
    right: 0;
    top: 126px;
    display: flex;
    justify-content: center;
    align-items: center;
    gap: 12px;
    font-family: "Roboto Condensed", "Arial Narrow", sans-serif;
    font-weight: 700;
    font-size: 40px;
    line-height: 1;
    color: var(--white);
  }
  .back-brand-square {
    width: 16px;
    height: 16px;
    background: var(--white);
  }
  .services {
    position: absolute;
    left: 0;
    right: 0;
    top: 257px;
    margin: 0;
    text-align: center;
    font-family: "Roboto", Arial, sans-serif;
    font-size: 14.5px;
    line-height: 18px;
    color: var(--white);
  }
</style>
</head>
<body>
<main class="canvas">
  <section class="card card-front" aria-label="Card front">
    <div class="brand"><span class="brand-square"></span>GIRDERLINE</div>

    <svg class="name-flag" width="34" height="39" viewBox="0 0 34 39" aria-hidden="true">
      <polygon points="0,0 34,0 26,39 0,39" fill="var(--brand-red)"/>
    </svg>

    <div class="person">
      <h1 class="person-name">DANIEL HARROW</h1>
      <p class="person-title">CEO/FOUNDER</p>
    </div>

    <ul class="contact-list">
      <li>
        <svg class="contact-icon" viewBox="0 0 16 16" aria-hidden="true">
          <path d="M3.5 1.5 L6 4.5 L4.6 6.2 C5.5 8 7.8 10.4 9.8 11.4 L11.5 10 L14.5 12.5 L12.8 14.6 C7.5 14 2 8.5 1.4 3.2 Z" fill="var(--brand-red)"/>
        </svg>
        555 013 2946
      </li>
      <li>
        <svg class="contact-icon" viewBox="0 0 16 16" aria-hidden="true">
          <rect x="1" y="3.5" width="14" height="9" fill="var(--brand-red)"/>
          <polyline points="1.5,4 8,9 14.5,4" fill="none" stroke="var(--card-front)" stroke-width="1.3"/>
        </svg>
        info@girderline.com
      </li>
      <li>
        <svg class="contact-icon" viewBox="0 0 16 16" aria-hidden="true">
          <circle cx="8" cy="8" r="6.5" fill="var(--brand-red)"/>
          <path d="M5 4.5 C6.5 5 6 7 7.5 7.5 C8.5 8 8 10 9 11.5 M10.5 3.5 C10 5 11.5 5.5 12.5 6" fill="none" stroke="var(--card-front)" stroke-width="1.2"/>
        </svg>
        www.girderline.com
      </li>
    </ul>
  </section>

  <section class="card card-back" aria-label="Card back">
    <div class="back-brand"><span class="back-brand-square"></span>GIRDERLINE</div>
    <p class="services">
      Pipelines • Rail • Infrastructure • Forestry<br>
      Power • Northgate • Ridgeford • Port Alderby<br>
      Cedarvale • Westhaven
    </p>
  </section>
</main>
</body>
</html>
```